Super elegant, crisp & clean Business card design required

We recently upgraded our branding - which is on our website - talvendoraphoto.com

I would like a simple, yet elegant, clean business card design please.

The font of my logo is Cinzel - and because of the natural colour - it's best to have this on a black background.

I would like to have the back of the business card - with simply my logo.

PLEASE DO NOT SUBMIT A COMPLICATED / UNCLEAN DESIGN

Industry/Entity Type

Business

Contact Information for Business Card

Talven Doroshko Photography

Font styles to use
Other font styles liked:
• Cinzel

Requirements
Must have
• A backpage with nothing but my logo
• Simple design - stands out
Should not have
• Colour that dont align with my logo
• Over complicated '/ non symmetrical design

```html
<!DOCTYPE html>
<html lang="en">
<head>
<meta charset="utf-8">
<title>Talven Doroshko Photography — Business Card</title>
<link rel="stylesheet" href="https://fonts.googleapis.com/css2?family=Cinzel:wght@400&family=Questrial&display=swap">
<style>
  :root {
    --backdrop: #161616;
    --card: #000000;
    --gold: #8c7b5e;
    --gold-soft: #7d6d52;
  }
  * { margin: 0; padding: 0; box-sizing: border-box; }
  html, body {
    width: 1200px;
    height: 741px;
    overflow: hidden;
    background: var(--backdrop);
  }
  .canvas {
    position: relative;
    width: 1200px;
    height: 741px;
  }
  .card {
    position: absolute;
    top: 229px;
    width: 494px;
    height: 282px;
    background: var(--card);
    color: var(--gold);
    overflow: hidden;
  }
  .card--back { left: 99px; }
  .card--front { left: 609px; }

  .brand {
    position: absolute;
    display: flex;
    flex-direction: column;
    align-items: center;
    transform: translateX(-50%);
  }
  .brand__mark { display: block; }
  .brand__name {
    font-family: "Cinzel", serif;
    font-weight: 400;
    color: var(--gold);
    white-space: nowrap;
    line-height: 1;
    text-align: center;
  }
  .brand__line { display: block; }
  .brand__sub {
    display: block;
    letter-spacing: 0.75em;
    margin-right: -0.75em;
  }

  .card--back .brand { left: 247px; top: 68px; }
  .card--back .brand__name { font-size: 22px; margin-top: 26px; }
  .card--back .brand__sub { font-size: 10px; margin-top: 3px; }

  .card--front .brand { left: 127px; top: 24px; }
  .card--front .brand__name { font-size: 20px; margin-top: 18px; }
  .card--front .brand__sub { font-size: 9px; margin-top: 3px; }

  .divider {
    position: absolute;
    left: 244px;
    top: 162px;
    width: 1px;
    height: 97px;
    background: var(--gold-soft);
  }
  .person {
    position: absolute;
    left: 255px;
    top: 160px;
  }
  .person__name {
    font-family: "Cinzel", serif;
    font-size: 18px;
    line-height: 1;
    color: var(--gold);
    letter-spacing: 0.02em;
  }
  .person__role {
    font-family: "Questrial", sans-serif;
    font-size: 13px;
    margin-top: 3px;
    color: var(--gold);
  }
  .contacts {
    position: absolute;
    left: 255px;
    top: 211px;
    list-style: none;
    font-family: "Questrial", sans-serif;
    font-size: 13px;
    color: var(--gold);
    white-space: nowrap;
  }
  .contacts__item {
    display: flex;
    align-items: center;
    height: 17px;
  }
  .contacts__icon {
    width: 11px;
    height: 11px;
    margin-right: 8px;
    flex: none;
  }
</style>
</head>
<body>
<main class="canvas">

  <section class="card card--back" aria-label="Card back">
    <div class="brand">
      <svg class="brand__mark" width="96" height="96" viewBox="0 0 96 96" aria-hidden="true">
        <circle cx="48" cy="48" r="46" fill="none" stroke="var(--gold)" stroke-width="1.5"/>
      </svg>
      <p class="brand__name">
        <span class="brand__line">Talven Doroshko</span>
        <span class="brand__sub">Photography</span>
      </p>
    </div>
  </section>

  <section class="card card--front" aria-label="Card front">
    <div class="brand">
      <svg class="brand__mark" width="88" height="88" viewBox="0 0 88 88" aria-hidden="true">
        <circle cx="44" cy="44" r="42" fill="none" stroke="var(--gold)" stroke-width="1.5"/>
      </svg>
      <p class="brand__name">
        <span class="brand__line">Talven Doroshko</span>
        <span class="brand__sub">Photography</span>
      </p>
    </div>

    <span class="divider" aria-hidden="true"></span>

    <div class="person">
      <p class="person__name">ELIAS VARN</p>
      <p class="person__role">Chief Executive Officer</p>
    </div>

    <ul class="contacts">
      <li class="contacts__item">
        <svg class="contacts__icon" viewBox="0 0 12 12" aria-hidden="true">
          <path d="M3 1 L4.6 1 L5.2 3.6 L4 4.4 C4.6 6 5.8 7.3 7.4 8 L8.3 6.8 L11 7.4 L11 9 C11 10.2 10 11 8.8 10.8 C5 10.2 1.8 7 1.2 3.2 C1 2 1.8 1 3 1 Z" fill="var(--gold)"/>
        </svg>
        44 7700 900418
      </li>
      <li class="contacts__item">
        <svg class="contacts__icon" viewBox="0 0 12 12" aria-hidden="true">
          <rect x="0.5" y="2" width="11" height="8" fill="var(--gold)"/>
          <path d="M0.8 2.4 L6 6.6 L11.2 2.4" fill="none" stroke="#000" stroke-width="0.9"/>
        </svg>
        td.studio@talvendoraphoto.com
      </li>
      <li class="contacts__item">
        <svg class="contacts__icon" viewBox="0 0 12 12" aria-hidden="true">
          <circle cx="6" cy="6" r="5.2" fill="none" stroke="var(--gold)" stroke-width="1"/>
          <ellipse cx="6" cy="6" rx="2.3" ry="5.2" fill="none" stroke="var(--gold)" stroke-width="0.8"/>
          <path d="M0.8 6 H11.2 M1.6 3.4 H10.4 M1.6 8.6 H10.4" stroke="var(--gold)" stroke-width="0.7"/>
        </svg>
        www.talvendoraphoto.com
      </li>
    </ul>
  </section>

</main>
</body>
</html>
```